3rd Annual Suds & Wags Fundraiser

This is our 3rd Annual Suds & Wags Dog Wash Extravagana to support Helpers of Tamsin Valley Pet Center. Please see the attached flyer for the 2nd Annual. We loved this flyer! Please revamp with our logo attached and the new content provided. Let's keep to the same colors as the 2nd Annual flyer-no change. Date: Saturday April 25th 2020 10A-1PM. Rain Date: May 2nd. Same address as 2nd Annual.

Other font styles liked:
• See 2nd Annual Flyer

Colors
add136
e34297
6b449b

Requirements
Must have
• See attached 2nd annual flyer including colors
Nice to have

```html
<!DOCTYPE html>
<html lang="en">
<head>
<meta charset="utf-8">
<title>Suds &amp; Wags – Third Annual</title>
<link rel="stylesheet" href="https://fonts.googleapis.com/css2?family=Fredoka:wght@500;600;700&family=Arimo:ital,wght@0,400;0,700;1,400&family=Libre+Baskerville:wght@700&display=swap">
<style>
  :root{
    --green:#9dcc3f;
    --pink:#e34297;
    --purple:#8a6bb4;
    --purple-deep:#6b449b;
    --ink:#1c1c1c;
    --stage:#5c5c5c;
    --band-grey:#ececec;
    --button-blue:#3d6bb3;
    --white:#ffffff;
  }
  *{box-sizing:border-box;margin:0;padding:0}
  html,body{width:1200px;height:1200px;overflow:hidden;background:var(--stage)}
  body{font-family:"Arimo",Arial,sans-serif;color:var(--ink)}
  .flyer{position:absolute;left:229px;top:75px;width:742px;height:1049px;background:var(--white);overflow:hidden}
  .art{position:absolute;inset:0;width:742px;height:1049px}
  .layer{position:absolute}
  .badge{left:54px;top:350px;width:112px;height:112px;border-radius:50%;background:var(--pink);color:var(--white);
    font-family:"Fredoka",sans-serif;font-weight:600;font-size:25px;line-height:23px;display:flex;align-items:center;justify-content:center;text-align:center}
  .title{left:28px;top:470px;font-family:"Fredoka",sans-serif;font-weight:700;font-size:50px;letter-spacing:-1px;line-height:1;color:var(--purple)}
  .tagline{left:30px;top:523px;color:var(--pink);font-family:"Fredoka",sans-serif;font-weight:500;font-size:12.5px;letter-spacing:6.4px;white-space:nowrap}
  .family-bar{left:0;top:546px;width:478px;height:38px;background:var(--purple);border-radius:0 19px 19px 0;color:var(--white);
    font-weight:700;font-size:22px;line-height:38px;padding-left:29px}
  .support{left:513px;top:382px;font-family:"Fredoka",sans-serif;font-weight:600;font-size:19px;letter-spacing:2px}
  .partner{left:500px;top:420px;width:200px;height:110px;display:flex;align-items:center;justify-content:center;text-align:center;
    font-weight:700;font-size:22px;line-height:26px;color:var(--ink)}
  .partner-line{left:480px;top:547px;width:240px;text-align:center;font-family:"Libre Baskerville",Georgia,serif;font-weight:700;font-size:11.5px;line-height:18px}
  .label{font-family:"Fredoka",sans-serif;font-weight:600;color:var(--pink);font-size:24px;line-height:28px}
  .date-label{left:28px;top:604px} .time-label{left:28px;top:667px}
  .when{left:106px;font-weight:700;font-size:23px;line-height:28px}
  .when-date{top:607px} .when-time{top:670px}
  .loc-label{left:466px;top:592px}
  .loc{left:466px;top:625px;font-size:14px;line-height:18px}
  .loc strong{font-family:"Fredoka",sans-serif;font-weight:600;font-size:15px}
  .perks{left:0;top:704px;width:742px;height:81px;background:var(--green)}
  .perk-col{position:absolute;top:11px;list-style:none;font-size:15px;line-height:20.5px}
  .perk-col li{display:flex;gap:6px;align-items:flex-start}
  .perk-col svg{flex:none;margin-top:3px}
  .c1{left:28px}.c2{left:289px}.c3{left:485px}
  .donate{left:0;top:785px;width:742px;height:41px;background:var(--band-grey)}
  .donate > *{position:absolute}
  .donate-note{left:28px;top:9px;font-size:10px;line-height:11.5px}
  .donate-arrow{left:104px;top:14px}
  .donate-web{left:132px;top:8px;font-size:21px;line-height:24px;white-space:nowrap}
  .donate-web b{font-weight:700}
  .donate-btn{left:392px;top:7px;height:27px;width:133px;text-align:center;background:var(--button-blue);color:var(--white);font-weight:700;font-size:18px;line-height:27px}
  .notice{left:0;top:826px;width:742px;height:47px;background:var(--green);padding:7px 0 0 28px;font-style:italic;font-size:13.5px;line-height:17px}
  .contact{top:887px;width:230px;text-align:center;font-size:13.5px;line-height:17px}
  .contact h3{font-family:"Fredoka",sans-serif;font-weight:600;color:var(--pink);font-size:19px;line-height:26px;margin-bottom:2px}
  .contact b{font-weight:700}
  .contact-a{left:27px} .contact-b{left:264px}
  .divider{left:271px;top:903px;width:1px;height:86px;background:#bbb}
  .mark{top:990px;width:230px;text-align:center;font-weight:700;font-size:16px;line-height:19px;color:var(--ink)}
  .mark-a{left:27px}
  .mark-b{left:264px}
</style>
</head>
<body>
<main class="flyer">
  <svg class="art" viewBox="0 0 742 1049">
    <defs>
      <linearGradient id="crowd" x1="0" y1="0" x2="0" y2="1">
        <stop offset="0" stop-color="#6f9a52"/><stop offset="0.5" stop-color="#7a7f8c"/><stop offset="1" stop-color="#8c8e92"/>
      </linearGradient>
      <linearGradient id="warm" x1="0" y1="0" x2="1" y2="1">
        <stop offset="0" stop-color="#a58a6c"/><stop offset="1" stop-color="#6e7a6a"/>
      </linearGradient>
      <linearGradient id="shepherd" x1="0" y1="0" x2="0" y2="1">
        <stop offset="0" stop-color="#6f9a4a"/><stop offset="0.45" stop-color="#8a6a45"/><stop offset="1" stop-color="#b7aa9a"/>
      </linearGradient>
    </defs>
    <path role="img" aria-label="Photo of volunteers with a dog mascot at last year's dog wash" fill="url(#crowd)"
      d="M0 0H742V300L400 392C250 372 110 356 0 345Z"/>
    <path fill="var(--green)" d="M0 372C130 392 260 404 430 394L430 406C260 418 120 412 0 398Z"/>
    <circle role="img" aria-label="Photo of a volunteer at a treats table" cx="653" cy="173" r="118" fill="#8fa3ad" stroke="var(--pink)" stroke-width="5"/>
    <circle role="img" aria-label="Photo of the mascot holding a free doggie wash sign" cx="553" cy="270" r="92" fill="url(#warm)" stroke="var(--purple)" stroke-width="5"/>
    <circle role="img" aria-label="Photo of a family with their dog" cx="422" cy="325" r="82" fill="#7d8f9a" stroke="var(--pink)" stroke-width="5"/>
    <circle role="img" aria-label="Photo of a spaniel being washed" cx="303" cy="353" r="62" fill="#9a7256" stroke="var(--purple)" stroke-width="4"/>
  </svg>

  <div class="layer badge">Third<br>Annual</div>
  <h1 class="layer title">Suds &amp; Wags</h1>
  <p class="layer tagline">DO A LITTLE. CHANGE A LOT.</p>
  <div class="layer family-bar">A FAMILY FUN EVENT FOR ALL AGES</div>

  <p class="layer support">IN SUPPORT OF</p>
  <div class="layer partner">Helpers of Tamsin Valley Pet Center</div>
  <p class="layer partner-line">Adopt a forever friend …<br>You will be their hero</p>

  <span class="layer label date-label">Date:</span>
  <p class="layer when when-date">Saturday, April 25, 2020<br>Rain Date: May 2nd</p>
  <span class="layer label time-label">Time:</span>
  <p class="layer when when-time">10AM - 1PM</p>

  <span class="layer label loc-label">Location:</span>
  <p class="layer loc"><strong>Harbor Lane Realty</strong><br>418 Commons Way<br>Cedar Bay FL 32990<br>Bayside Town Center</p>

  <section class="layer perks">
    <ul class="perk-col c1">
      <li><svg width="16" height="14" viewBox="0 0 16 14"><rect x="1" y="2" width="11" height="11" fill="none" stroke="#fff" stroke-width="1.8"/><path d="M4 7l3 3 8-9" fill="none" stroke="#fff" stroke-width="2"/></svg>FREE Doggie Wash</li>
      <li><svg width="16" height="14" viewBox="0 0 16 14"><rect x="1" y="2" width="11" height="11" fill="none" stroke="#fff" stroke-width="1.8"/><path d="M4 7l3 3 8-9" fill="none" stroke="#fff" stroke-width="2"/></svg>Food &amp; Beverages</li>
      <li><svg width="16" height="14" viewBox="0 0 16 14"><rect x="1" y="2" width="11" height="11" fill="none" stroke="#fff" stroke-width="1.8"/><path d="M4 7l3 3 8-9" fill="none" stroke="#fff" stroke-width="2"/></svg>Vendors (FREE give-a-ways)</li>
    </ul>
    <ul class="perk-col c2">
      <li><svg width="16" height="14" viewBox="0 0 16 14"><rect x="1" y="2" width="11" height="11" fill="none" stroke="#fff" stroke-width="1.8"/><path d="M4 7l3 3 8-9" fill="none" stroke="#fff" stroke-width="2"/></svg>Raffle Drawings</li>
      <li><svg width="16" height="14" viewBox="0 0 16 14"><rect x="1" y="2" width="11" height="11" fill="none" stroke="#fff" stroke-width="1.8"/><path d="M4 7l3 3 8-9" fill="none" stroke="#fff" stroke-width="2"/></svg>Live Music</li>
      <li><svg width="16" height="14" viewBox="0 0 16 14"><rect x="1" y="2" width="11" height="11" fill="none" stroke="#fff" stroke-width="1.8"/><path d="M4 7l3 3 8-9" fill="none" stroke="#fff" stroke-width="2"/></svg>Donations Welcome</li>
    </ul>
    <ul class="perk-col c3">
      <li><svg width="16" height="14" viewBox="0 0 16 14"><rect x="1" y="2" width="11" height="11" fill="none" stroke="#fff" stroke-width="1.8"/><path d="M4 7l3 3 8-9" fill="none" stroke="#fff" stroke-width="2"/></svg><span>Adoptions by<br>HTVPC</span></li>
    </ul>
  </section>

  <div class="layer donate">
    <span class="donate-note">TO MAKE<br>A DONATION</span>
    <svg class="donate-arrow" width="8" height="12" viewBox="0 0 8 12"><path d="M1 1l5 5-5 5" fill="none" stroke="var(--green)" stroke-width="2"/></svg>
    <span class="donate-web">tamsinvalleypets.org/<b>give</b></span>
    <span class="donate-btn">Donate Now</span>
  </div>

  <p class="layer notice">All domestic breeds from puppies to seniors invited. Please be sure Furry Fido<br>is tolerant of other dogs, crowds and bathing.</p>

  <div class="layer contact contact-a">
    <h3>Dana Whitfield</h3>
    <p>Harbor Lane Realty Co.<br><b>555.210.4417</b><br>dana@harborlanerealty.com</p>
  </div>
  <div class="layer divider"></div>
  <div class="layer contact contact-b">
    <h3>Mara Ellison</h3>
    <p>HTVPC<br><b>555.380.2219</b><br>mara.ellison@example.net</p>
  </div>
  <div class="layer mark mark-a">Harbor Lane<br>Realty</div>
  <div class="layer mark mark-b">Helpers of Tamsin<br>Valley Pet Center</div>

  <svg class="art" viewBox="0 0 742 1049" style="pointer-events:none">
    <path fill="var(--purple-deep)" d="M742 700C590 742 485 870 460 1049H478C502 884 602 766 742 728Z"/>
    <path role="img" aria-label="Photo of a wet German shepherd at the wash" fill="url(#shepherd)" d="M742 728C602 766 502 884 478 1049H742Z"/>
  </svg>
</main>
</body>
</html>
```